The Linen Loft Co

We need a business card design for our wardrobe company.
Please visit our website www.gentlelinenlofts.com to get an idea of who we are.

```html
<!DOCTYPE html>
<html lang="en">
<head>
<meta charset="utf-8">
<title>The Linen Loft Co — Business Card</title>
<link rel="stylesheet" href="https://fonts.googleapis.com/css2?family=Open+Sans:wght@400;600&display=swap">
<style>
  :root {
    --backdrop: #95cbbf;
    --card: #161616;
    --frame: #5a5a5a;
    --brand-grey: #5e5e5e;
    --tagline-grey: #6a6a6a;
    --contact: #f2f2f2;
  }
  * { margin: 0; padding: 0; box-sizing: border-box; }
  html, body {
    width: 1200px;
    height: 800px;
    overflow: hidden;
    background: var(--backdrop);
  }
  .canvas {
    position: relative;
    width: 1200px;
    height: 800px;
  }
  .card {
    position: absolute;
    left: 240px;
    top: 190px;
    width: 720px;
    height: 410px;
    background: var(--card);
    border-radius: 16px;
    font-family: "Open Sans", sans-serif;
  }
  .card-frame {
    position: absolute;
    inset: 26px 22px 24px 22px;
    border: 2px solid var(--frame);
    border-radius: 10px;
  }
  .brand {
    position: absolute;
    left: 54px;
    top: 150px;
  }
  .brand-name {
    font-size: 21px;
    font-weight: 400;
    letter-spacing: 0.5px;
    text-transform: uppercase;
    color: var(--brand-grey);
  }
  .brand-tagline {
    margin-top: 10px;
    margin-left: 27px;
    font-size: 19px;
    font-weight: 400;
    color: var(--tagline-grey);
  }
  .contact-list {
    position: absolute;
    left: 262px;
    top: 266px;
    list-style: none;
  }
  .contact-item {
    display: flex;
    align-items: center;
    height: 25.5px;
    font-size: 16.5px;
    font-weight: 600;
    color: var(--contact);
  }
  .contact-icon {
    width: 12px;
    height: 12px;
    margin-right: 10px;
    fill: var(--contact);
    flex: none;
  }
</style>
</head>
<body>
<main class="canvas">
  <section class="card" aria-label="Business card front">
    <div class="card-frame"></div>

    <div class="brand">
      <p class="brand-name">The Linen Loft Co</p>
      <p class="brand-tagline">Crafted for Every Corner</p>
    </div>

    <ul class="contact-list">
      <li class="contact-item">
        <svg class="contact-icon" viewBox="0 0 12 12" aria-hidden="true">
          <path d="M6 0.5a3.6 3.6 0 0 0-3.6 3.6c0 2.7 3.6 7.4 3.6 7.4s3.6-4.7 3.6-7.4A3.6 3.6 0 0 0 6 0.5zm0 5a1.4 1.4 0 1 1 0-2.8 1.4 1.4 0 0 1 0 2.8z"/>
        </svg>
        Harbour Court, 42 Mill Lane, London N1 4QT
      </li>
      <li class="contact-item">
        <svg class="contact-icon" viewBox="0 0 12 12" aria-hidden="true">
          <path d="M1 4.2C1 2.6 3.3 1.5 6 1.5s5 1.1 5 2.7v1H8.4V3.9H3.6v1.3H1zM3.2 5.6h5.6l1.6 4.6H1.6z"/>
        </svg>
        0207 555 0148
      </li>
      <li class="contact-item">
        <svg class="contact-icon" viewBox="0 0 12 12" aria-hidden="true">
          <path d="M1 2.5h10v7H1zM1.6 3.1 6 6.6l4.4-3.5z" fill-rule="evenodd"/>
        </svg>
        info@gentlelinenlofts.com
      </li>
      <li class="contact-item">
        <svg class="contact-icon" viewBox="0 0 12 12" aria-hidden="true">
          <path d="M6 0.8a5.2 5.2 0 1 0 0 10.4A5.2 5.2 0 0 0 6 0.8zm0 1.2c.6.7 1.1 1.8 1.2 3.4H4.8C4.9 3.8 5.4 2.7 6 2zM2.1 6.6h1.6c.1 1.3.4 2.4.9 3.2a4 4 0 0 1-2.5-3.2zm0-1.2a4 4 0 0 1 2.5-3.2c-.5.8-.8 1.9-.9 3.2zM6 10c-.6-.7-1.1-1.8-1.2-3.4h2.4C7.1 8.2 6.6 9.3 6 10zm1.4-.2c.5-.8.8-1.9.9-3.2h1.6a4 4 0 0 1-2.5 3.2zm.9-4.4c-.1-1.3-.4-2.4-.9-3.2a4 4 0 0 1 2.5 3.2z"/>
        </svg>
        gentlelinenlofts.com
      </li>
    </ul>
  </section>
</main>
</body>
</html>
```